Lurvik.no is a new website about pedagogical entrepreneurship. It's main target group is teachers. The Nordic Bureau for Digital Schooling and the National Office for Learning and Classrooms are leading the project.

The web page is meant to show examples of how different methods of entrepreneurship can be used pedagogical in a learning environment. The page will also support the user with examples of different teaching programs and other examples of best practice.

Pedagogical entrepreneurship is not about business and men in suits. It's a method for learning. The focus in the design should be on school, education and new ways of learning.

The final product should be motivating and engaging, but at the same time governmental and serious. We are not looking for something "flashy" and corporate-looking, but a moderate, task-focused and clean design that state quality.

We need designs for three pages:
1 - frontpage
2 - subpage ("Metoder og undervisningsopplegg")
3 - subpage ("Små-TOPP i Vassbygd")

The interaction design for these three pages will be uploaded as an attachment.

We would like you to find inspiration in the following websites:
- www.skapekraft.no
- www.giellu.no
- www.brightfernlab.com
- www.zyx.no
(more will be added)

Please use the attached logo, and feel free to use this as an inspiration for the rest of the design.

Target Market(s)

Teachers

Industry/Entity Type

Education

Requirements
Must have
• * Header with: Logo. Main navigation. Utility navigation. Search box.
* Footer
Should not have
• Images of men in suits.
Very strong graphical elements that stands out too much (we want it clean).

```html
<!DOCTYPE html>
<html lang="en">
<head>
<meta charset="utf-8">
<title>Lurvik.no – Pedagogical Entrepreneurship</title>
<link href="https://fonts.googleapis.com/css2?family=Arimo:wght@400;700&display=swap" rel="stylesheet">
<style>
  :root{
    --ink:#333;
    --ink-soft:#555;
    --brand:#0c4f7e;
    --hero-top:#0d5a8c;
    --hero-bottom:#063a73;
    --footer:#0b4a72;
    --footer-link:#8fd0f5;
    --chevron:#1a6fb0;
    --rule:#d9d9d9;
    --panel:#f5f5f5;
    --paper:#ffffff;
  }
  *{box-sizing:border-box;margin:0;padding:0}
  html,body{width:1031px;height:1200px;overflow:hidden;background:var(--paper)}
  body{font-family:"Arimo",Arial,sans-serif;color:var(--ink)}
  .page{width:1000px;height:1164px;transform:scale(1.031);transform-origin:0 0;position:relative}
  a{color:inherit}

  /* header */
  .site-header{height:60px;position:relative;background:linear-gradient(#fff,#f4f4f4);border-bottom:1px solid #e4e4e4}
  .main-nav{position:absolute;left:381px;top:21px;font-size:13px;color:#333;display:flex}
  .main-nav .sep{margin:0 16px;color:#666}
  .search{position:absolute;left:816px;top:18px;width:167px;height:27px;border:1px solid #bbb;border-radius:5px;background:#fff;box-shadow:inset 0 1px 2px rgba(0,0,0,.12)}
  .search span{position:absolute;left:10px;top:7px;font-size:11px;font-style:italic;color:#999}
  .search svg{position:absolute;right:7px;top:6px}

  /* hero */
  .hero{position:absolute;top:60px;left:0;width:1000px;height:378px;background:radial-gradient(ellipse at 70% 40%,var(--hero-top),var(--hero-bottom) 75%);overflow:hidden}
  .hero-lines{position:absolute;inset:0}
  .brand{position:absolute;left:40px;top:125px;display:flex;align-items:center;gap:14px}
  .brand-dot{width:58px;height:58px;border-radius:50%;background:#e9eef3}
  .brand-name{font-size:46px;font-weight:700;color:#5aa6e3;letter-spacing:-1px}
  .hero-lead{position:absolute;left:414px;top:38px;width:480px;font-size:18px;line-height:30px;color:#fff}
  .learn-more{position:absolute;left:813px;top:85px;font-size:13px;color:#cfe6f7;text-decoration:none}
  .bubble{position:absolute;top:141px;width:175px;height:175px;border-radius:50%;background:#f1f1f1;border:3px solid #d8dde2;text-align:center}
  .bubble .icon{display:block;width:54px;height:56px;margin:4px auto 0;border-radius:8px}
  .bubble h3{font-weight:400;font-size:14.5px;line-height:24px;color:#555;margin-top:2px}
  .bubble p{font-size:13px;line-height:20px;color:var(--brand);margin-top:8px}

  /* get started */
  .meter-card{position:absolute;left:24px;top:456px;width:263px;height:250px;border:1px solid var(--rule);border-radius:3px;background:linear-gradient(#fff,var(--panel))}
  .meter-card h2{position:absolute;left:19px;top:14px;font-weight:400;font-size:15px;line-height:24px;color:var(--brand)}
  .gauge{position:absolute;left:42px;top:70px;width:146px;height:124px;border-radius:6px;background:linear-gradient(135deg,#dfe3ec 0%,#d6d6d6 50%,#e6d8d8 100%)}
  .meter-card a{position:absolute;left:51px;top:216px;font-size:13px;color:var(--brand)}
  .start-title{position:absolute;left:347px;top:474px;font-weight:400;font-size:15px;color:var(--brand)}
  .link-col{position:absolute;top:511px}
  .link-col h4{font-weight:400;font-size:13.5px;color:#333;margin-bottom:11px}
  .link-col ul{list-style:none}
  .link-col li{font-size:12.5px;color:#444;height:24px;padding-left:12px;position:relative}
  .link-col li::before{content:"";position:absolute;left:0;top:4px;width:5px;height:5px;border-right:2px solid var(--chevron);border-top:2px solid var(--chevron);transform:rotate(45deg)}
  .link-col .more{display:block;font-size:10.5px;color:var(--brand);margin:6px 0 0 11px}
  .divider{position:absolute;left:0;width:1000px;height:1px;background:var(--rule)}

  /* inspiration */
  .insp-title{position:absolute;left:35px;top:745px;font-weight:400;font-size:15px;color:var(--brand)}
  .arrow{position:absolute;top:817px;width:18px;height:18px;border-radius:50%;background:#444}
  .arrow svg{display:block}
  .case{position:absolute;top:774px;display:flex;gap:16px}
  .case .photo{width:167px;height:114px;border:1px solid #ddd;padding:3px;background:#fff;border-radius:3px}
  .case .photo div{width:100%;height:100%}
  .case p{font-size:13px;line-height:24px;color:#444;margin-top:30px}

  /* footer */
  .site-footer{position:absolute;top:903px;left:0;width:1000px;height:214px;background:var(--footer);color:#fff}
  .footer-brand{position:absolute;left:14px;top:52px;font-size:22px;font-weight:700;color:#cde4f4}
  .foot-col{position:absolute;top:24px}
  .foot-col h5{font-weight:400;font-size:13px;margin-bottom:20px}
  .foot-col a{display:block;font-size:12px;color:var(--footer-link);line-height:24px}
  .foot-col .more{color:#fff;font-size:10.5px;margin-top:6px}
  .legal{position:absolute;top:1117px;left:0;width:1000px;height:47px;background:linear-gradient(#fff,#f0f0f0);text-align:center;font-size:10.5px;color:#666;padding-top:18px}
</style>
</head>
<body>
<div class="page">

  <header class="site-header">
    <nav class="main-nav">
      <span>Best practice Schools</span><span class="sep">|</span>
      <span>Lurvometer</span><span class="sep">|</span>
      <span>About Lurvik no</span>
    </nav>
    <div class="search"><span>Search...</span>
      <svg width="14" height="14" viewBox="0 0 14 14"><circle cx="6" cy="6" r="4.5" fill="#5aa9e6" stroke="#2a6db0" stroke-width="1.5"/><line x1="9.2" y1="9.2" x2="13" y2="13" stroke="#2a6db0" stroke-width="2"/></svg>
    </div>
  </header>

  <section class="hero">
    <svg class="hero-lines" width="1000" height="378" viewBox="0 0 1000 378" aria-hidden="true">
      <g stroke="#ffffff" stroke-opacity=".06" fill="none">
        <path d="M380 0 L520 378"/><path d="M560 0 L700 378"/><path d="M760 0 L980 378"/>
        <path d="M300 378 C500 260 800 260 1000 200"/><path d="M0 260 C200 200 400 160 640 180"/>
      </g>
    </svg>
    <div class="brand"><span class="brand-dot"></span><span class="brand-name">Lurvik</span></div>
    <p class="hero-lead">Pedagogical entrepreneurship and the methods, and find inspiration and teaching plans.</p>
    <a class="learn-more" href="#">Learn More &gt;&gt;</a>

    <div class="bubble" style="left:381px">
      <span class="icon" role="img" aria-label="Illustration of a teacher holding books" style="background:linear-gradient(#c0562a,#3a7bc8)"></span>
      <h3>What is Pedagocicial<br>Entrepreneurship?</h3>
      <p>Learn about what,<br>&nbsp;&nbsp;&nbsp;&nbsp;why and how!</p>
    </div>
    <div class="bubble" style="left:582px">
      <span class="icon" role="img" aria-label="Illustration of a classroom blackboard on a stand" style="background:linear-gradient(#3a3a3a,#5c9ad0)"></span>
      <h3>Methods and<br>Teaching Plans</h3>
      <p>Plan your lessons!</p>
    </div>
    <div class="bubble" style="left:783px">
      <span class="icon" role="img" aria-label="Illustration of a student reading a book" style="background:linear-gradient(#8b5a3a,#2d6fb8)"></span>
      <h3>Good Examples /<br>Best Practice</h3>
      <p>Be inspired!</p>
    </div>
  </section>

  <div class="divider" style="top:440px"></div>

  <aside class="meter-card">
    <h2>Are you working<br>Entrepreneurship-like?</h2>
    <div class="gauge" role="img" aria-label="Illustration of a measuring dial gauge"></div>
    <a href="#">Try the Lurvometer!</a>
  </aside>

  <h2 class="start-title">Get Started!</h2>
  <div class="link-col" style="left:356px">
    <h4>Methods</h4>
    <ul><li>Cafe - pedagogikk</li><li>Elevbedrift</li><li>Grundercamp</li><li>Story line</li><li>Real</li></ul>
    <a class="more" href="#">See More ...</a>
  </div>
  <div class="link-col" style="left:588px">
    <h4>Teaching Plans</h4>
    <ul><li>Teachning Plan Title</li><li>Teachning Plan Title</li><li>Teachning Plan Title</li><li>Teachning Plan Title</li><li>Teachning Plan Title</li></ul>
    <a class="more" href="#">See More ...</a>
  </div>
  <div class="link-col" style="left:817px;top:512px">
    <h4>Teaching Plans</h4>
    <ul><li>Teachning Plan Title</li><li>Teachning Plan Title</li><li>Teachning Plan Title</li><li>Teachning Plan Title</li><li>Teachning Plan Title</li></ul>
    <a class="more" href="#">See More ...</a>
  </div>

  <div class="divider" style="top:728px"></div>

  <h2 class="insp-title">Inspiration</h2>
  <span class="arrow" style="left:10px"><svg width="18" height="18"><path d="M10.5 5.5 L7 9 L10.5 12.5" stroke="#fff" stroke-width="1.6" fill="none"/></svg></span>
  <span class="arrow" style="left:962px"><svg width="18" height="18"><path d="M7.5 5.5 L11 9 L7.5 12.5" stroke="#fff" stroke-width="1.6" fill="none"/></svg></span>

  <div class="case" style="left:39px">
    <div class="photo"><div role="img" aria-label="Photo of a red brick school building with lawn" style="background:linear-gradient(#b9cde4 0%,#9a5a48 45%,#6f8a4a 100%)"></div></div>
    <p>Små-TOPP at<br>Vassbygd School</p>
  </div>
  <div class="case" style="left:349px">
    <div class="photo"><div role="img" aria-label="Photo of a sand-coloured school entrance" style="background:linear-gradient(#9fc2e6 0%,#c98f4e 40%,#b7773c 100%)"></div></div>
    <p>Små-TOPP at<br>Vassbygd School</p>
  </div>
  <div class="case" style="left:660px">
    <div class="photo"><div role="img" aria-label="Photo of a modern school building with palm trees" style="background:linear-gradient(#a9bfd6 0%,#d7d3c8 45%,#7d9463 80%,#c9a27a 100%)"></div></div>
    <p>Små-TOPP at<br>Vassbygd School</p>
  </div>

  <footer class="site-footer">
    <span class="footer-brand">Lurvik</span>
    <div class="foot-col" style="left:158px">
      <h5>Pedagogical Entrepreneurship</h5>
      <a href="#">What is pedagogical entrepreneurship?</a><a href="#">Science</a><a href="#">Best practice schools</a><a href="#">Lurvometeret</a><a href="#">About lurvik.no</a>
    </div>
    <div class="foot-col" style="left:449px">
      <h5>Methods</h5>
      <a href="#">Story line</a><a href="#">Real</a><a href="#">Cafe-pedagogikk</a><a class="more" href="#">See More ...</a>
    </div>
    <div class="foot-col" style="left:620px">
      <h5>Teaching plans</h5>
      <a href="#">Title</a><a href="#">Title</a><a href="#">Title</a><a class="more" href="#">See More ...</a>
    </div>
    <div class="foot-col" style="left:801px">
      <h5>Gode Eksempler</h5>
      <a href="#">Små-TOPP at vassbygd School</a><a href="#">Små-TOPP at vassbygd School</a><a href="#">Små-TOPP at vassbygd School</a><a class="more" href="#">See More ...</a>
    </div>
  </footer>
  <div class="legal">© 2012 Lurvik, All Rights Reserved</div>

</div>
</body>
</html>
```